Open Harbor book needs a cover design

I need a front and back cover design that demonstrates a strong sense of possibility that trust can be repaired even if things look bleak. Repairing trust is difficult, but this book is full of wisdom, proven strategies, and doctoral research to help people strengthen relationships and improve trust. It can help any group: business, nonprofit, education, service. Showing diversity of groups and people is very important. For the cover title, there should be a play on words: "Open Harbor: Is it? Within Reach" should have the words "is it?" crossed out and the words "It IS! should be replaced there in a striking way. Perhaps in red ink. For publishing purposes, book will be titled Open Harbor: It IS Within Reach! Please see the attachment for an example. The book layout is approximately 260 pages.

A business self-help book, but the target is any person in a group that feels they have lost trust in each other. It can be just a normal person struggling in a volunteer group they are a part of, or a supervisor whose group is not working well together. It can be a leader who just wants their group to be stronger.

Business Management

• Allise - I believe is being used on the interior of the book for the title page and headings

• Show hope and possibility in the midst of difficulty. Must have a play on the words in the title "Open Harbor: Is it? Within Reach" with crossing out "is it?" with "It IS!" (see attached example) Must include the author's name: Marla Quentin, PhD Must include a smaller tagline: "Practical Steps to Move Teams Forward Again"
• Showing diverse people, or hands. Diverse kinds of groups - not just business. A colorful cover. Maybe show the complexity of trust when it is broken...broken pieces of trust that are then picked up and put together when people work together. Could show people (or images of hands) or other ways to show that it's a choice and it is possible to repair broken trust. I'd also like to convey a sense of a group - not just random people. That they have something at stake to work on repairing trust together and this book can help them.
• If images of people are used, just showing one gender or race is not okay. Nor just binary choices: like an image containing one man and one woman, or one white person and one person of color - otherwise it seems that the book on Open Harbor is about race or gender relations.

```html
<!DOCTYPE html>
<html lang="en">
<head>
<meta charset="utf-8">
<title>Open Harbor — Book Cover</title>
<link href="https://fonts.googleapis.com/css2?family=Yanone+Kaffeesatz:wght@300;400&display=swap" rel="stylesheet">
<style>
  :root {
    --bg: #ece9e4;
    --paper: #ffffff;
    --ink: #1c1c1c;
    --teal: #2aa9c2;
    --teal-band: #35afc8;
    --red: #d8262b;
    --rule: #5a5a5a;
  }
  * { margin: 0; padding: 0; box-sizing: border-box; }
  html, body { width: 1200px; height: 800px; overflow: hidden; background: var(--bg); }
  body { display: flex; align-items: center; justify-content: center; font-family: "Yanone Kaffeesatz", sans-serif; }

  .cover {
    position: relative;
    width: 480px;
    height: 736px;
    background: var(--paper);
    overflow: hidden;
    box-shadow: 0 4px 18px rgba(0,0,0,0.12);
  }

  .group-seated {
    position: absolute; left: 0; top: 0; width: 100%; height: 270px;
    background: linear-gradient(180deg, #e2e2e2 0%, #cfd3d8 35%, #e8e6e2 70%, #ffffff 100%);
    opacity: 0.85;
  }
  .group-table {
    position: absolute; left: 0; top: 445px; width: 100%; height: 225px;
    background: linear-gradient(90deg, #c0463f 0%, #e8c35a 18%, #6b7a8c 35%, #b05b6f 50%, #3f9a4c 68%, #2d5fa8 85%, #e6d2b4 100%);
  }
  .group-table::after {
    content: ""; position: absolute; inset: 0;
    background: linear-gradient(180deg, rgba(255,255,255,0.9) 0%, rgba(255,255,255,0) 22%, rgba(255,255,255,0) 60%, rgba(226,205,176,0.7) 100%);
  }

  .title {
    position: absolute; left: 150px; top: 82px; width: 250px;
    text-align: center; line-height: 0.86; font-weight: 400;
  }
  .title-top { display: block; font-size: 86px; color: var(--ink); letter-spacing: 1px; }
  .title-bottom { display: block; font-size: 86px; color: var(--teal); letter-spacing: 1px; }

  .play {
    position: absolute; left: 0; width: 100%; text-align: center; color: var(--ink);
  }
  .play-yes { top: 262px; font-size: 50px; font-weight: 400; }
  .play-no { top: 322px; }
  .play-no svg { display: block; margin: 0 auto; }
  .play-main { top: 346px; font-size: 54px; font-weight: 400; }

  .tagline {
    position: absolute; left: 88px; width: 304px; top: 414px;
    border-top: 1px solid var(--rule); border-bottom: 1px solid var(--rule);
    padding: 6px 0 5px; text-align: center;
    font-size: 22px; font-weight: 300; line-height: 1.05; color: var(--ink); letter-spacing: 0.3px;
  }

  .author-band {
    position: absolute; left: 0; bottom: 0; width: 100%; height: 66px;
    background: var(--teal-band); color: var(--paper);
    display: flex; align-items: center; justify-content: center;
    font-size: 32px; font-weight: 400; letter-spacing: 0.5px;
  }
</style>
</head>
<body>
  <main class="cover">
    <div class="group-seated" role="img" aria-label="Faded photo of a diverse group of people seated in a row against a white wall"></div>
    <div class="group-table" role="img" aria-label="Colorful photo of a diverse team working together around a table with books and a plant"></div>

    <h1 class="title">
      <span class="title-top">OPEN</span>
      <span class="title-bottom">HARBOR</span>
    </h1>

    <p class="play play-yes">It Is!</p>
    <div class="play play-no">
      <svg width="70" height="26" viewBox="0 0 70 26" aria-label="Is It? crossed out">
        <text x="35" y="20" text-anchor="middle" font-family="Yanone Kaffeesatz, sans-serif" font-size="24" fill="#1c1c1c">Is It?</text>
        <line x1="6" y1="6" x2="64" y2="20" stroke="#d8262b" stroke-width="2"/>
        <line x1="6" y1="20" x2="64" y2="6" stroke="#d8262b" stroke-width="2"/>
      </svg>
    </div>
    <p class="play play-main">Within Reach</p>

    <p class="tagline">PRACTICAL STEPS TO MOVE<br>TEAMS FORWARD AGAIN</p>

    <footer class="author-band">Marla Quentin, PhD</footer>
  </main>
</body>
</html>
```